New, modern business card for growing audiology practice

We need a new business card for our audiology practice. Our logo and website have recently changed (more modern) and we want our business cards to reflect this change.
We conduct hearing tests, perform earwax removals, and fit & dispense hearing aids to our patients. We are a family owned practice in which the owner is the one who works directly with the patient. I have attached logos in various formats to use, as well as two ideas I found on this website; as well as a scanned copy of our current logo. Good luck!

Industry/Entity Type

Business

Contact Information for Business Card

Company name: Tolvera Hearing Center
Provider name: Peter Wolstenby, Au.D. F/NSB
Phone number: (440) 683-5127
Address: 837 W. Lindell Ave. Marrowdale, OH 44097
email: tolverahearing@postvane.com
website: tolverahearing.com

Colors
000000
aaaaaa
dbdbdb
cacaca
9bcb3c
afd23c
cadf82
b1b1b1

Requirements
Must have
• My card must include information in the "details" section. In the attached images, I found a few that I liked and I would like to model after - "brisky bouncin'" and "Sound Method Center".
• Must be horizontal.
• Must include logos provided. I uploaded them in various file formats and various ways.
• Must match logo font, if possible, if not, please get as close as you can.
Nice to have
• I really like the idea of having a color on one side with just the logo and company name and the contact information and provider name on the other side. I also really like the idea of having the main color dominating on the logo/company side with accent of that same color on the contact side of the card.
Should not have
• Must not be vertical.

```html
<!DOCTYPE html>
<html lang="en">
<head>
<meta charset="utf-8">
<title>Tolvera Hearing Center – Business Card</title>
<link href="https://fonts.googleapis.com/css2?family=Lato:wght@400;700&family=PT+Sans:wght@400;700&display=swap" rel="stylesheet">
<style>
  :root {
    --stage: #000000;
    --card-front: #ffffff;
    --ink: #1d1d1b;
    --green: #9bcb3c;
    --green-bright: #afd23c;
    --green-deep: #a9cc3a;
    --green-soft: #cadf82;
  }
  * { box-sizing: border-box; margin: 0; padding: 0; }
  html, body {
    width: 1200px; height: 900px; overflow: hidden;
    background: var(--stage);
  }
  .canvas { position: relative; width: 1200px; height: 900px; }
  .card {
    position: absolute; top: 306px;
    width: 439px; height: 271px;
    border-radius: 10px; overflow: hidden;
  }
  .card--front { left: 149px; background: var(--card-front); }
  .card--back { left: 608px; background: var(--green-bright); }

  .brand {
    position: absolute; left: 22px; top: 44px;
    display: flex; align-items: center; gap: 12px;
  }
  .brand__dot {
    width: 30px; height: 30px; border-radius: 50%;
    background: var(--green);
  }
  .brand__name {
    font-family: "Lato", sans-serif; font-weight: 400;
    font-size: 22px; letter-spacing: 0.2px;
    color: var(--ink); text-transform: uppercase;
  }

  .provider {
    position: absolute; left: 23px; top: 126px;
    font-family: "PT Sans", sans-serif;
    color: var(--ink); font-size: 13px;
  }
  .provider__name {
    color: var(--green); font-weight: 700; font-size: 15px;
    text-transform: uppercase; letter-spacing: 0.3px;
  }

  .contact {
    position: absolute; left: 23px; top: 157px;
    font-family: "PT Sans", sans-serif; font-size: 13px;
    line-height: 16px; color: var(--ink); list-style: none;
  }
  .contact__item { display: flex; gap: 5px; align-items: flex-start; }
  .contact__item--address { margin-bottom: 8px; }
  .contact__icon { width: 10px; height: 10px; margin-top: 3px; flex: none; fill: var(--green); }

  .back__pattern {
    position: absolute; inset: 0;
    background: radial-gradient(circle at 50% 50%, var(--green-bright), var(--green-deep));
  }
  .back__brand {
    position: absolute; left: 0; right: 0; top: 126px;
    text-align: center;
    font-family: "Lato", sans-serif; font-weight: 400;
    font-size: 14px; letter-spacing: 0.4px;
    color: #ffffff; text-transform: uppercase;
  }
</style>
</head>
<body>
<main class="canvas">
  <section class="card card--front">
    <div class="brand">
      <span class="brand__dot"></span>
      <span class="brand__name">Tolvera Hearing Center</span>
    </div>

    <p class="provider"><span class="provider__name">Peter Wolstenby</span>, AU.D. F/NSB</p>

    <ul class="contact">
      <li class="contact__item contact__item--address">
        <svg class="contact__icon" viewBox="0 0 10 10"><path d="M5 0a3.5 3.5 0 0 0-3.5 3.5C1.5 6 5 10 5 10s3.5-4 3.5-6.5A3.5 3.5 0 0 0 5 0zm0 5a1.4 1.4 0 1 1 0-2.8A1.4 1.4 0 0 1 5 5z"/></svg>
        <span>837 W. Lindell<br>Ave. Marrowdale, OH 44097</span>
      </li>
      <li class="contact__item">
        <svg class="contact__icon" viewBox="0 0 10 10"><path d="M2.2 0.5l1.6 2-1 1.2c.6 1.4 1.9 2.7 3.4 3.4l1.2-1 2 1.6-1 1.8C4.6 9.4.6 5.4.5 1.5z"/></svg>
        <span>(440) 683-5127</span>
      </li>
      <li class="contact__item">
        <svg class="contact__icon" viewBox="0 0 10 10"><path d="M0.5 2h9v6h-9zM1 2.5l4 3 4-3"/></svg>
        <span>tolverahearing@postvane.com</span>
      </li>
      <li class="contact__item">
        <svg class="contact__icon" viewBox="0 0 10 10"><circle cx="5" cy="5" r="4.5"/><path d="M2 4h6v0.8H2zM2.5 6h5v0.8h-5z" fill="#ffffff"/></svg>
        <span>www.tolverahearing.com</span>
      </li>
    </ul>
  </section>

  <section class="card card--back">
    <div class="back__pattern" role="img" aria-label="Repeating light pattern of the practice mark across the green back"></div>
    <p class="back__brand">Tolvera Hearing Center</p>
  </section>
</main>
</body>
</html>
```